Design of Labels for Harbour Reef Gin bottle

Design bottle labels for Harbour Reef Gin. There are three labels to design; a front, a back and a tamper band to be placed over the cork. The labels should be deigned to fit the bottle specified in the link below.
The Gin is an excellent high end premium brand Navy strength Gin 57% Vol. The bottle should evoke excellence and a romance of period of pride in the British Navy. Gin was drunk by officers in the Navy so a representation of the Officer Class should be made possibly through gold braid of a senior officer's sleeve, cap or lapel. The white ensign should also be prominent. Suggested colour themes are navy blues, grey, and white....although others schemes may be suitable. Corley's Dock Rum is a good example of the sort of thing we are looking for, although the design must not be so similar that it encroaches on Corley's trade mark or copyrights. The period theme is 1900 to 1940
Bottle link: https://www.vessel-crate-depot.co.uk/Glass-bottles/350ml-flint-glass-bottle-Marta.html
Target Market(s)
Gin Drinkers
Look and feel
Each slider illustrates characteristics of the customer's brand and the style your logo design should communicate.

```html
<!DOCTYPE html>
<html lang="en">
<head>
<meta charset="utf-8">
<title>Harbour Reef Gin – Front Label</title>
<link rel="stylesheet" href="https://fonts.googleapis.com/css2?family=Cinzel:wght@700&family=Pinyon+Script&family=Oswald:wght@400&family=Libre+Caslon+Text&display=swap">
<style>
  :root {
    --backdrop: #e4e5e8;
    --label-white: #f4f4f2;
    --navy: #2b3039;
    --navy-ink: #22262e;
    --gold: #c9a24a;
    --gold-soft: #b8913f;
    --rope-white: #eceef0;
    --grey-tab: #4a4d52;
  }
  html, body {
    margin: 0;
    padding: 0;
    width: 1200px;
    height: 1200px;
    overflow: hidden;
    background: var(--backdrop);
  }
  .canvas {
    position: relative;
    width: 1200px;
    height: 1200px;
  }
  .label {
    position: absolute;
    left: 160px;
    top: 0;
    width: 920px;
    height: 1200px;
  }
  .label svg { display: block; }
  .brand-arc {
    font-family: "Cinzel", serif;
    font-weight: 700;
    font-size: 112px;
    letter-spacing: 6px;
    fill: var(--navy-ink);
  }
  .tab-text {
    font-family: "Libre Caslon Text", serif;
    font-size: 24px;
    fill: #ffffff;
  }
  .brand-main {
    font-family: "Cinzel", serif;
    font-weight: 700;
    font-size: 122px;
    fill: #f2f2f0;
  }
  .tagline {
    font-family: "Pinyon Script", cursive;
    font-size: 74px;
    fill: var(--gold);
  }
  .spec {
    font-family: "Oswald", sans-serif;
    font-size: 34px;
  }
  .spec-light { fill: #e8e8e6; }
  .spec-gold { fill: var(--gold); }
</style>
</head>
<body>
<div class="canvas">
  <div class="label">
    <svg width="920" height="1200" viewBox="160 0 920 1200" xmlns="http://www.w3.org/2000/svg">
      <defs>
        <path id="brand-arc-path" d="M 200 584 A 440 440 0 0 1 1080 584"/>
        <linearGradient id="coil-tone" x1="0" y1="0" x2="0" y2="1">
          <stop offset="0" stop-color="#6b717c"/>
          <stop offset="1" stop-color="#565b66"/>
        </linearGradient>
        <linearGradient id="crest-tone" x1="0" y1="0" x2="1" y2="1">
          <stop offset="0" stop-color="#cfb57a"/>
          <stop offset="1" stop-color="#8d8c8e"/>
        </linearGradient>
      </defs>

      <!-- upper white panel -->
      <rect class="panel-white" x="160" y="0" width="920" height="588" fill="var(--label-white)"/>
      <!-- lower navy panel -->
      <rect class="panel-navy" x="160" y="588" width="920" height="612" fill="var(--navy)"/>

      <!-- frame lines: dark on white panel -->
      <g class="frame-upper" fill="none" stroke="var(--navy-ink)" stroke-width="3">
        <line x1="194" y1="0" x2="194" y2="588"/>
        <line x1="220" y1="0" x2="220" y2="588"/>
        <line x1="1006" y1="0" x2="1006" y2="588"/>
        <line x1="1032" y1="0" x2="1032" y2="588"/>
      </g>
      <!-- frame lines: white on navy panel -->
      <g class="frame-lower" fill="none" stroke="var(--rope-white)" stroke-width="3">
        <line x1="194" y1="588" x2="194" y2="1200"/>
        <line x1="220" y1="588" x2="220" y2="1200"/>
        <line x1="1006" y1="588" x2="1006" y2="1200"/>
        <line x1="1032" y1="588" x2="1032" y2="1200"/>
      </g>

      <!-- arched brand word -->
      <text class="brand-arc">
        <textPath href="#brand-arc-path" startOffset="50%" text-anchor="middle">HARBOUR</textPath>
      </text>

      <!-- crest area -->
      <rect class="crest" x="360" y="272" width="544" height="266" rx="120"
            fill="url(#crest-tone)" opacity="0.55"
            role="img" aria-label="Heraldic crest: crown, crossed anchors, rope ring with anchor and two gold rampant lions"/>

      <!-- established tabs -->
      <g class="est-tab">
        <rect x="248" y="316" width="92" height="36" fill="var(--grey-tab)"/>
        <text class="tab-text" x="294" y="342" text-anchor="middle">EST.</text>
      </g>
      <g class="year-tab">
        <rect x="924" y="330" width="80" height="38" fill="var(--grey-tab)"/>
        <text class="tab-text" x="964" y="357" text-anchor="middle">2018</text>
      </g>

      <!-- coiled rope illustration area -->
      <rect class="rope-coil" x="334" y="604" width="594" height="228" rx="14"
            fill="url(#coil-tone)"
            role="img" aria-label="Illustration of a white coiled rope laid in four rows with a loop on top"/>

      <!-- product name -->
      <text class="brand-main" x="632" y="982" text-anchor="middle">REEF GIN</text>

      <!-- tagline -->
      <text class="tagline" x="632" y="1068" text-anchor="middle">Premium Blend</text>

      <!-- gold rule -->
      <line class="rule" x1="336" y1="1110" x2="928" y2="1110" stroke="var(--gold-soft)" stroke-width="2"/>

      <!-- specs row -->
      <text class="spec spec-light" x="334" y="1190">57 % vol</text>
      <text class="spec spec-gold" x="636" y="1180" text-anchor="middle">PRODUCT OF ENGLAND</text>
      <text class="spec spec-light" x="928" y="1170" text-anchor="end">350 ml</text>
    </svg>
  </div>
</div>
</body>
</html>
```